skyPARLOR Helicopter Tour WordPress Website Design

SkyPARLOR (skyparlor-example.com) is a premium helicopter tour company offering scenic flights in two Florida cities: Tampa and Sarasota. We are seeking a full Wordpress website redesign that is modern, upbeat, inviting, and highly conversion‑focused. The new site should feel energetic and trustworthy, reflect the excitement of helicopter sightseeing, and maintain our recognizable SkyPARLOR color palette—while updating the overall look to feel fresh, clean, and current.
The website must be SEO‑friendly, mobile‑optimized, and easy to navigate. It should highlight our 5‑star customer reviews, showcase our tours clearly, and integrate seamlessly with TrailDock for instant online booking. The design should support a premium aviation experience while remaining friendly and accessible to tourists, families, couples, and adventure seekers.

These elements are essential and must be included in the design:

Brand & UX:
- Modern, upbeat, inviting design
- SEO‑friendly structure and layout
- Easy navigation and clear user flow
- Light grey “SP” background logo watermark (as used on current site)
- Clean, aviation‑inspired typography and layout

Conversion Features:
- Instant booking above the fold (TrailDock integration)
- Live Orbin Ratings carousel
- Tour comparison table (duration, route, price, etc.)
- FAQ expandable section
- Gift Cards page (highlighted as a major offering)
- What to Expect timeline (Arrive → Check‑In → Safety Briefing → Flight → Photos)
- Weather transparency widget (clear messaging about weather‑dependent flights

Content Structure:
- Separate pages for Tampa, Sarasota, and Gender Reveal Flights
- Pilot/Team profiles with short bios
- Highlighted features:
- Doors‑Off option
- Sunset flights
- Romantic packages
- Champagne add‑ons

Colors:
Use the existing SkyPARLOR palette as the foundation, but modernize it.
- Background: Clean with the light grey “SP” watermark integrated tastefully.
The overall color direction should feel bright, premium, energetic, and trustworthy

Target Market(s)

Tourists visiting Tampa or Sarasota, Families looking for memorable activities, Couples seeking romantic experiences (sunset flights, proposals, anniversaries), Adventure seekers and content creators, Locals celebrating birthdays, holidays, or special occasions, Gender reveal clients looking for a unique aerial reveal experience

Industry/Entity Type

Travel & Tourism / Aviation / Helicopter Tours / Experience‑based Activities

Requirements
Must have
• These elements are essential and must be included in the design: Brand & UX - Modern, upbeat, inviting design / SEO‑friendly structure and layout / Easy navigation and clear user flow / Light grey “SP” background logo watermark (as used on current site) / Clean, aviation‑inspired typography and layout
Nice to have
• Interactive route map showing flight paths / Subtle motion or parallax effects in hero sections / Animated icons or micro‑interactions / Social media integration (Instagram grid, TikTok clips) / Sticky mobile booking bar / Video header or short aerial footage loop / Subtle aviation‑themed graphic elements (rotor blur, sky gradients, etc.
Should not have
• No dark, heavy, or overly moody themes / No outdated fonts or overly playful typography / No cluttered layouts or excessive text blocks / No stocky, generic tourism imagery / No slow‑loading animations or heavy effects that hurt SEO

```html
<!DOCTYPE html>
<html lang="en">
<head>
<meta charset="utf-8">
<title>SkyPARLOR – Featured Experiences</title>
<link href="https://fonts.googleapis.com/css2?family=Rajdhani:wght@500;600;700&family=Mulish:wght@400;600&display=swap" rel="stylesheet">
<style>
  :root{
    --blue:#1b46d4;
    --ink:#1c1d22;
    --muted:#6b6e76;
    --white:#ffffff;
    --page:#ffffff;
    --hero-a:#1d3a44;
    --hero-b:#6b5a45;
    --hero-c:#c9ad86;
    --photo-a:#d9dde2;
    --photo-b:#b7a48f;
  }
  *{box-sizing:border-box;margin:0;padding:0}
  html,body{width:1200px;height:872px;overflow:hidden;background:var(--page)}
  body{position:relative;font-family:'Mulish',sans-serif;color:var(--ink)}

  .hero{
    position:absolute;left:0;top:0;width:1200px;height:390px;
    background:
      linear-gradient(rgba(10,20,28,.45),rgba(10,20,28,.35)),
      linear-gradient(115deg,var(--hero-a) 0%,#2f5862 30%,var(--hero-b) 62%,var(--hero-c) 100%);
  }
  .hero-head{position:absolute;top:70px;left:0;width:100%;text-align:center;color:var(--white)}
  .eyebrow{
    display:inline-flex;align-items:center;gap:12px;
    font-family:'Rajdhani',sans-serif;font-weight:600;font-size:15px;letter-spacing:.3px;
  }
  .eyebrow::before,.eyebrow::after{content:"";width:22px;height:2px;background:currentColor}
  .hero-title{
    margin-top:12px;font-family:'Rajdhani',sans-serif;font-weight:700;
    font-size:46px;line-height:1.15;
  }

  .experiences{
    position:absolute;top:255px;left:180px;width:840px;
    display:flex;gap:30px;
  }
  .card{
    position:relative;flex:1;height:300px;background:var(--white);
    box-shadow:0 14px 40px rgba(20,30,60,.12);
    text-align:center;padding:48px 30px 0;
  }
  .card svg{width:78px;height:62px;stroke:var(--blue);fill:none;stroke-width:2.4;stroke-linecap:round;stroke-linejoin:round}
  .card-title{
    margin-top:22px;font-family:'Rajdhani',sans-serif;font-weight:700;font-size:21px;color:var(--ink);
  }
  .card-text{margin-top:16px;font-size:13px;line-height:1.85;color:var(--muted)}
  .corner{position:absolute;bottom:-12px;width:22px;height:22px;border-bottom:4px solid var(--blue)}
  .corner.left{left:-12px;border-left:4px solid var(--blue)}
  .corner.right{right:-12px;border-right:4px solid var(--blue)}

  .expect{position:absolute;top:660px;left:180px}
  .expect .label{
    display:flex;align-items:center;gap:10px;color:var(--blue);
    font-family:'Rajdhani',sans-serif;font-weight:600;font-size:15px;
  }
  .expect .label::before{content:"";width:22px;height:2px;background:var(--blue)}
  .expect h2{margin-top:10px;font-family:'Rajdhani',sans-serif;font-weight:700;font-size:40px;color:var(--ink)}

  .expect-photo{
    position:absolute;top:650px;left:620px;width:370px;height:222px;
    background:linear-gradient(135deg,var(--photo-a) 0%,#eef0f3 45%,var(--photo-b) 100%);
  }
  .expect-frame{
    position:absolute;top:636px;left:862px;width:142px;height:236px;
    border-top:14px solid var(--blue);border-right:14px solid var(--blue);
  }
</style>
</head>
<body>
  <section class="hero" role="img" aria-label="Photo of a smiling pilot and passenger seated in a helicopter cockpit"></section>

  <header class="hero-head">
    <p class="eyebrow">Featured Experiences</p>
    <h1 class="hero-title">More Ways to Fly With<br>SkyPARLOR</h1>
  </header>

  <section class="experiences">
    <article class="card">
      <svg viewBox="0 0 78 62" aria-hidden="true">
        <path d="M10 8h58M39 8v8"/>
        <path d="M24 20h26c8 0 14 6 14 14s-6 10-14 10H32c-5 0-8-4-8-9V20z"/>
        <path d="M50 20v13h14"/>
        <path d="M24 28H6M6 22v12"/>
        <path d="M34 44v8M54 44v8M26 52h38"/>
      </svg>
      <h3 class="card-title">Doors-Off Flights</h3>
      <p class="card-text">An open-air helicopter experience for pure adrenaline, crystal-clear views, and epic photos.</p>
      <span class="corner left"></span><span class="corner right"></span>
    </article>

    <article class="card">
      <svg viewBox="0 0 78 62" aria-hidden="true">
        <path d="M22 34a17 17 0 0 1 34 0z"/>
        <path d="M14 40h50M18 47h42M24 54h30"/>
        <path d="M39 6v6M21 13l4 4M57 13l-4 4"/>
      </svg>
      <h3 class="card-title">Sunset &amp; Romantic Flights</h3>
      <p class="card-text">Golden hour skies, a smooth ride, and unforgettable moments — perfect for couples.</p>
      <span class="corner left"></span><span class="corner right"></span>
    </article>

    <article class="card">
      <svg viewBox="0 0 78 62" aria-hidden="true">
        <path d="M24 10l10 3-4 16c-1 4-6 5-9 2l-3-3z"/>
        <path d="M25 31l-5 22M14 52l12 3"/>
        <path d="M54 10l-10 3 4 16c1 4 6 5 9 2l3-3z"/>
        <path d="M53 31l5 22M52 55l12-3"/>
        <path d="M36 4l2 4M42 3l-1 5M30 6l3 3"/>
      </svg>
      <h3 class="card-title">Champagne Add-Ons</h3>
      <p class="card-text">Celebrate birthdays, anniversaries, and special occasions with a premium touch.</p>
      <span class="corner left"></span><span class="corner right"></span>
    </article>
  </section>

  <section class="expect">
    <p class="label">What to Expect</p>
    <h2>Your Helicopter</h2>
  </section>

  <div class="expect-photo" role="img" aria-label="Photo of a pilot preparing guests beside a helicopter"></div>
  <div class="expect-frame"></div>
</body>
</html>
```